Desktop and Networking Support Course 9.17.25

Important the ad should not be very busy with the text taking up the major part of the ad .. please do not make the text so big that it takes up most of the ad..
Flyer Design Brief for Graphic Artist
also i am looking for something unique or creative that it will stand out .
Size & Layout:
Full Page with Bleed: 8” x 10.75” + 0.25” bleed on all sides.
Footer Space: Leave a 1-inch margin at the bottom for footer content (e.g., contact info, logo, or call-to-action).
Target Audience:
College-age students (around 24 years old)
Located in the USA
Interested in creative, professional, and career-building opportunities
Purpose:
To attract students to enroll in a college program
Flyer should be eye-catching, unique, and creative
Text must be clear and readable,
Design Style:
Use vector art, typography, or photography — your choice
If using photography, feature a white young professional USA citizen:
Wearing a white collared shirt
not with long hair
Creative Direction:
The flyer should stand out visually — something people would want to look at and keep
Showcase creativity and professionalism
Use bold colors, dynamic layout, or unexpected design elements to grab attention
Avoid clutter — keep the design balanced and clean
Text Suggestions (can be adjusted):
Footer,
please leave one inch on the bottom for the footer

```html
<!DOCTYPE html>
<html lang="en">
<head>
<meta charset="utf-8">
<title>Desktop &amp; Network Support Course Flyer</title>
<link rel="stylesheet" href="https://fonts.googleapis.com/css2?family=Poppins:ital,wght@0,400;0,600;0,700;1,400&display=swap">
<style>
  :root {
    --stage: #1b2039;
    --paper: #ffffff;
    --orange: #f58b4c;
    --navy: #27358f;
    --green: #6cc895;
    --white: #ffffff;
    --panel-teal: #3ea5cc;
    --panel-purple: #2a2466;
    --panel-blue: #27389a;
  }
  * { margin: 0; padding: 0; box-sizing: border-box; }
  html, body {
    width: 1200px; height: 1200px; overflow: hidden;
    background: var(--stage);
    font-family: "Poppins", sans-serif;
  }
  .flyer {
    position: absolute; left: 214px; top: 90px;
    width: 771px; height: 1020px;
    background: var(--paper);
    overflow: hidden;
  }
  .hero-photo {
    position: absolute; left: 301px; top: 0; width: 470px; height: 374px;
    background: radial-gradient(ellipse 60% 65% at 55% 45%, #e8b690 0%, #f1cdb2 35%, #d5dbef 62%, #f6f7fb 82%, #ffffff 100%);
  }
  .headline { position: absolute; left: 47px; top: 34px; line-height: 1; }
  .headline-lead {
    display: block; color: var(--orange); font-weight: 700;
    font-size: 43px; line-height: 53px; letter-spacing: -0.3px;
  }
  .headline-key {
    display: block; color: var(--navy); font-weight: 700;
    font-size: 80px; line-height: 76px; letter-spacing: -1px; margin-top: 6px;
  }
  .panel { position: absolute; left: 0; top: 0; width: 771px; height: 880px; }
  .network-art {
    position: absolute; left: 593px; top: 404px; width: 178px; height: 434px;
    background: radial-gradient(ellipse 70% 45% at 70% 55%, rgba(220,232,210,0.28) 0%, rgba(198,112,104,0.14) 45%, rgba(108,200,149,0) 80%);
  }
  .course-title {
    position: absolute; left: 60px; top: 393px; height: 48px; white-space: nowrap;
    color: var(--white); font-weight: 700; font-size: 27.5px; line-height: 48px; letter-spacing: -0.3px;
  }
  .course-tag {
    position: absolute; left: 152px; top: 452px; width: 422px; height: 30px;
    background: var(--green); color: var(--white);
    font-size: 23px; line-height: 30px; text-align: center;
  }
  .stat-figure {
    position: absolute; left: 45px; top: 495px;
    color: var(--orange); font-weight: 700; font-size: 64px; line-height: 80px; letter-spacing: -1px;
  }
  .stat-label { position: absolute; left: 189px; top: 506px; color: var(--white); font-weight: 600; font-size: 22px; line-height: 30px; }
  .stat-note { position: absolute; left: 189px; top: 539px; color: var(--green); font-style: italic; font-size: 16.5px; line-height: 22px; }
  .jobs-label { position: absolute; left: 120px; top: 581px; color: var(--white); font-weight: 600; font-size: 22px; line-height: 30px; }
  .jobs-note { position: absolute; left: 120px; top: 614px; color: var(--green); font-style: italic; font-size: 16.5px; line-height: 22px; }
  .feature { position: absolute; top: 696px; }
  .feature-icon { width: 48px; height: 46px; display: block; }
  .feature-head { margin-top: 12px; color: var(--green); font-weight: 700; font-size: 18.5px; line-height: 28px; }
  .feature-text { color: var(--orange); font-size: 18.5px; line-height: 28px; }
  .feature-divider { position: absolute; top: 719px; width: 5px; height: 84px; border-radius: 3px; background: var(--orange); }
  .footer-band {
    position: absolute; left: 0; top: 860px; width: 771px; height: 20px;
    background: var(--orange); color: var(--white);
    font-size: 16.5px; line-height: 20px;
  }
  .footer-band span { position: absolute; top: 0; white-space: nowrap; }
  .footer-band b { font-weight: 700; }
</style>
</head>
<body>
  <div class="flyer">
    <div class="hero-photo" role="img" aria-label="Photo of a hand clicking a blue and silver computer mouse"></div>

    <h1 class="headline">
      <span class="headline-lead">Your Career<br>Is Just</span>
      <span class="headline-key">a Click<br>Away</span>
    </h1>

    <svg class="panel" viewBox="0 0 771 880" aria-hidden="true">
      <defs>
        <linearGradient id="panelFill" x1="0" y1="1" x2="1" y2="0">
          <stop offset="0" stop-color="var(--panel-teal)"/>
          <stop offset="0.35" stop-color="var(--panel-purple)"/>
          <stop offset="1" stop-color="var(--panel-blue)"/>
        </linearGradient>
      </defs>
      <polygon fill="url(#panelFill)"
        points="23,397 47,374 609,374 632,350 771,350 771,860 0,860 0,685 23,668"/>
      <path class="title-frame"
            d="M130,445 Q131,441 137,441 H558 Q566,441 566,433 V401 Q566,393 558,393 H56 Q48,393 48,401 V433 Q48,441 56,441 H86 L101,465 Q105,471 112,470 L118,468"
            fill="none" stroke="var(--orange)" stroke-width="3.5" stroke-linecap="round" stroke-linejoin="round"/>
      <polygon class="arrow-icon" points="53,609 104,596 77,637 73,621 55,633 52,628 67,615" fill="var(--orange)"/>
      <polyline points="23,666 364,666" fill="none" stroke="var(--green)" stroke-width="1.5"/>
      <polyline points="364,666 452,666 469,650" fill="none" stroke="var(--orange)" stroke-width="5" stroke-linecap="round"/>
      <polyline points="469,650 476,640 604,639" fill="none" stroke="var(--green)" stroke-width="1.5"/>
    </svg>

    <div class="network-art" role="img" aria-label="Decorative network of connected hexagons"></div>

    <h2 class="course-title">Desktop &amp; Network Support Course</h2>
    <p class="course-tag">Master Desktop Operating Systems</p>

    <p class="stat-figure">90%</p>
    <p class="stat-label">Employment Rate</p>
    <p class="stat-note">Class of 2024</p>

    <p class="jobs-label">Prepare for 3 of the Top 10 Tech Jobs</p>
    <p class="jobs-note">National Tech Careers Review 2025</p>

    <div class="feature" style="left:47px">
      <svg class="feature-icon" viewBox="0 0 48 46" fill="none" stroke="#fff" stroke-width="1.6" aria-hidden="true">
        <rect x="2" y="2" width="36" height="22"/><line x1="0" y1="26" x2="40" y2="26"/>
        <circle cx="20" cy="13" r="4"/><circle cx="10" cy="8" r="2"/><circle cx="29" cy="8" r="2"/>
        <circle cx="10" cy="33" r="2.5"/><circle cx="20" cy="33" r="2.5"/><circle cx="30" cy="33" r="2.5"/>
        <path d="M4,42 Q10,36 16,42 M14,42 Q20,36 26,42 M24,42 Q30,36 36,42"/><line x1="2" y1="43" x2="38" y2="43"/>
      </svg>
      <p class="feature-head">Hands-On</p>
      <p class="feature-text">Desktop &amp; Network<br>Training</p>
    </div>
    <div class="feature-divider" style="left:250px"></div>

    <div class="feature" style="left:279px">
      <svg class="feature-icon" viewBox="0 0 48 46" fill="none" stroke="#fff" stroke-width="1.6" aria-hidden="true">
        <circle cx="15" cy="26" r="8"/><path d="M12,34 V40 H18 V34 M13,43 H17"/>
        <path d="M3,22 H0 M15,12 V9 M6,15 L4,13 M24,15 L26,13"/>
        <circle cx="32" cy="7" r="5"/><path d="M30,7 L32,9 L35,5"/>
        <rect x="33" y="15" width="12" height="9"/><rect x="32" y="30" width="12" height="12"/>
      </svg>
      <p class="feature-head">Real-World</p>
      <p class="feature-text">Troubleshooting<br>Skills</p>
    </div>
    <div class="feature-divider" style="left:462px"></div>

    <div class="feature" style="left:491px">
      <svg class="feature-icon" viewBox="0 0 48 46" fill="none" stroke="#fff" stroke-width="1.6" aria-hidden="true">
        <path d="M2,10 H10 M2,14 H10 M2,18 H8"/>
        <circle cx="22" cy="12" r="7"/><path d="M11,40 Q11,24 22,24 Q33,24 33,40"/>
        <rect x="14" y="32" width="16" height="10" rx="1"/><line x1="10" y1="42" x2="34" y2="42"/>
        <path d="M36,10 L33,13 L36,16 M42,10 L45,13 L42,16 M40,9 L38,17"/>
      </svg>
      <p class="feature-head">Ready for</p>
      <p class="feature-text">IT Jobs</p>
    </div>

    <div class="footer-band">
      <span style="left:109px"><b>10</b> In-Person and Remote Options</span>
      <span style="left:405px"><b>|</b></span>
      <span style="left:434px"><b>Partial</b> Scholarships Offered</span>
    </div>
  </div>
</body>
</html>
```